Business Card Design Project

Business Card
We are rebranding with a new logo
Industry/Entity Type
Business
Contact Information for Business Card
Dennis Morvale +61 487215963 dennis@quorv.com.au P.O. Box 872 Fernlow QLD 4309
Requirements
Must have
- Logo

```html
<!DOCTYPE html>
<html lang="en">
<head>
<meta charset="utf-8">
<title>Quorv International – Business Card</title>
<link href="https://fonts.googleapis.com/css2?family=Roboto:wght@400;500&family=Roboto+Condensed:wght@500;700&display=swap" rel="stylesheet">
<style>
  :root {
    --backdrop: #2b2b2c;
    --card-white: #f2f2f2;
    --blue-deep: #0b4e6e;
    --blue-bright: #0d8fc4;
    --orange: #ee7a1f;
    --text-light: #ffffff;
  }
  * { margin: 0; padding: 0; box-sizing: border-box; }
  html, body {
    width: 1200px; height: 960px; overflow: hidden;
    background: var(--backdrop);
  }
  .card {
    position: absolute;
    left: 223px; top: 265px;
    width: 754px; height: 430px;
    border-radius: 22px;
    overflow: hidden;
    background: var(--card-white);
  }
  .card-art { position: absolute; inset: 0; }
  .brand {
    position: absolute;
    left: 62px; top: 162px;
    width: 270px;
    text-align: center;
    font-family: "Roboto Condensed", sans-serif;
    font-weight: 700;
    color: var(--blue-deep);
    line-height: 1;
  }
  .brand-name { display: block; font-size: 70px; letter-spacing: 1px; }
  .brand-tagline { display: block; font-size: 23px; letter-spacing: 4px; margin-top: 10px; }
  .contact {
    position: absolute;
    right: 46px; top: 222px;
    text-align: right;
    font-family: "Roboto", sans-serif;
    color: var(--text-light);
    font-size: 17px;
    line-height: 22px;
  }
  .contact-name {
    font-family: "Roboto Condensed", sans-serif;
    font-weight: 500;
    font-size: 27px;
    color: var(--orange);
    line-height: 30px;
    margin-bottom: 12px;
  }
  .contact-address { margin-bottom: 10px; }
  .contact-line { display: flex; justify-content: flex-end; align-items: center; gap: 8px; height: 24px; }
  .contact-line svg { width: 16px; height: 16px; fill: var(--orange); flex: none; }
</style>
</head>
<body>
  <div class="card">
    <svg class="card-art" viewBox="0 0 754 430" aria-hidden="true">
      <defs>
        <radialGradient id="blueGlow" cx="0.55" cy="0.35" r="0.75">
          <stop offset="0" stop-color="#0d8fc4"/>
          <stop offset="1" stop-color="#0b4e6e"/>
        </radialGradient>
      </defs>
      <path class="blue-panel" d="M520 0 H754 V430 H277 C430 300 530 160 520 0 Z" fill="url(#blueGlow)"/>
      <path class="divider-line" d="M512 0 C522 160 422 300 269 430" fill="none" stroke="#ee7a1f" stroke-width="8"/>
    </svg>

    <div class="brand">
      <span class="brand-name">Quorv</span>
      <span class="brand-tagline">INTERNATIONAL</span>
    </div>

    <div class="contact">
      <p class="contact-name">DENNIS MORVALE</p>
      <p class="contact-address">P.O. Box 872<br>Fernlow QLD 4309</p>
      <p class="contact-line">+61 487215963
        <svg viewBox="0 0 16 16"><path d="M3.5 1 6 3.8 4.8 6c.8 1.9 3.2 4.3 5.2 5.2l2.2-1.2L15 12.5 13.6 15C7.5 15 1 8.5 1 2.4Z"/></svg>
      </p>
      <p class="contact-line">dennis@quorv.com.au
        <svg viewBox="0 0 16 16"><path d="M1 3h14v10H1Z"/><path d="M1 3l7 6 7-6" fill="none" stroke="#0b4e6e" stroke-width="1.4"/></svg>
      </p>
      <p class="contact-line">www.quorv.com.au
        <svg viewBox="0 0 16 16"><circle cx="8" cy="8" r="7"/><path d="M1 8h14M8 1c-3 3-3 11 0 14M8 1c3 3 3 11 0 14" fill="none" stroke="#0b4e6e" stroke-width="1.1"/></svg>
      </p>
    </div>
  </div>
</body>
</html>
```